Young, dynamic furniture company needs a new business card design

We require a new business card design for our modern furniture company which supplies furniture and appliances to the property and development market.
Oakridge Interiors has become one of the leading furniture & appliance suppliers to the property market withing London. With over 10 years experience, we have increased our business to supply not only private landlords and managing agents, but also property developers, housing associations and local councils.
We offer not only a complete range of furniture which includes beds, wardrobes, dining sets and sofas, but also a high quality, full delivery and assembly service to help you with all our furnishing needs.

Target Market(s)

Private landlords, estate agents, letting agents, property management companies

Industry/Entity Type

Business

Contact Information for Business Card

Name,
Title,
Address,
Mobile,
Telephone,
Fax, Website, email address

Font styles to use
Sans Serif

Colors
3176b5
0555a3
85abd2
cfdeed

Requirements
Must have
• All the above information for each of our staff, along with our logo

```html
<!DOCTYPE html>
<html lang="en">
<head>
<meta charset="utf-8">
<title>Oakridge Interiors – Business Card</title>
<link href="https://fonts.googleapis.com/css2?family=Roboto:wght@400;500;700&display=swap" rel="stylesheet">
<style>
  :root {
    --bright-blue: #3176b5;
    --deep-blue: #0555a3;
    --navy: #1b3f8f;
    --mist-blue: #85abd2;
    --pale-blue: #cfdeed;
    --ink: #2a2a2e;
    --paper: #ffffff;
    --backdrop: #e9ebee;
  }
  * { box-sizing: border-box; margin: 0; padding: 0; }
  html, body {
    width: 1200px; height: 950px; overflow: hidden;
    background: var(--backdrop);
    font-family: "Roboto", Arial, sans-serif;
  }
  .stage { position: relative; width: 1200px; height: 950px; }

  .card {
    position: absolute; left: 250px; width: 700px; height: 400px;
    overflow: hidden; box-shadow: 0 6px 18px rgba(0,0,0,.18);
  }
  .card--back { top: 50px; background: var(--bright-blue); color: var(--paper); }
  .card--front { top: 500px; background: var(--paper); }

  .brand { position: absolute; text-align: center; }
  .brand__name { display: flex; align-items: center; justify-content: center; gap: 12px;
    font-weight: 700; font-size: 34px; letter-spacing: .5px; text-transform: uppercase; }
  .brand__square { width: 22px; height: 22px; background: currentColor; }
  .brand__tagline { margin-top: 8px; font-size: 14px; letter-spacing: 1.5px; text-transform: uppercase; }

  .card--back .brand { left: 0; right: 0; top: 140px; }
  .card--back .web { position: absolute; left: 0; right: 0; top: 285px; text-align: center;
    font-size: 17px; letter-spacing: 6px; }

  .card--front .brand { left: 20px; width: 290px; top: 170px; color: var(--ink); }
  .card--front .brand__name { font-size: 22px; gap: 9px; }
  .card--front .brand__name .brand__square { width: 16px; height: 16px; background: var(--deep-blue); }
  .card--front .brand__tagline { font-size: 10.5px; letter-spacing: 1.2px; color: #444; }

  .panel { position: absolute; left: 318px; top: 0; width: 382px; height: 400px; }
  .details { position: absolute; left: 372px; top: 58px; color: var(--paper); }
  .person__name { font-weight: 700; font-size: 22px; letter-spacing: .5px; text-transform: uppercase; }
  .person__title { font-size: 14px; margin-top: 4px; text-transform: uppercase; letter-spacing: .5px; }
  .address { margin-top: 44px; font-size: 16px; line-height: 1.35; }
  .contacts { list-style: none; margin-top: 14px; font-size: 15.5px; }
  .contacts li { display: flex; align-items: center; gap: 12px; height: 24px; }
  .contacts svg { width: 16px; height: 16px; flex: none; fill: var(--paper); }
</style>
</head>
<body>
<main class="stage">

  <section class="card card--back" aria-label="Card back">
    <div class="brand">
      <div class="brand__name"><span class="brand__square"></span>Oakridge Interiors</div>
      <div class="brand__tagline">Trade Furniture Solutions</div>
    </div>
    <div class="web">www.oakridgeinteriors.com</div>
  </section>

  <section class="card card--front" aria-label="Card front">
    <div class="brand">
      <div class="brand__name"><span class="brand__square"></span>Oakridge Interiors</div>
      <div class="brand__tagline">Trade Furniture Solutions</div>
    </div>

    <svg class="panel" viewBox="0 0 382 400" aria-hidden="true">
      <defs>
        <linearGradient id="panelFill" x1="0" y1="0" x2="1" y2="1">
          <stop offset="0" stop-color="#0555a3"/>
          <stop offset="1" stop-color="#1b3f8f"/>
        </linearGradient>
      </defs>
      <polygon points="16,0 382,0 382,400 16,400 16,108 8,100 16,92" fill="url(#panelFill)"/>
      <polyline points="6,0 6,86 0,100 6,114 6,400" fill="none" stroke="#3176b5" stroke-width="3"/>
    </svg>

    <div class="details">
      <div class="person__name">Daniel Marsh</div>
      <div class="person__title">President</div>
      <div class="address">2716 Harlow Lane<br>Millbrook, NY 12545</div>
      <ul class="contacts">
        <li><svg viewBox="0 0 16 16"><path d="M3 2h3l1 3-2 1c1 2 2 3 4 4l1-2 3 1v3c0 1-1 2-2 2C6 14 2 10 2 4c0-1 0-2 1-2z"/></svg>512 7730 4186</li>
        <li><svg viewBox="0 0 16 16"><path d="M4 1h8v14H4zM5.5 3v9h5V3zM7 13h2v1H7z" fill-rule="evenodd"/></svg>847 2901 6638</li>
        <li><svg viewBox="0 0 16 16"><path d="M4 1h7v4H4zM1 6h14v7h-2v2H3v-2H1zM5 10v3h6v-3z" fill-rule="evenodd"/></svg>839 5114 2707</li>
        <li><svg viewBox="0 0 16 16"><path d="M1 3h14v10H1zM2.5 4.5 8 9l5.5-4.5z" fill-rule="evenodd"/></svg>daniel@oakridgeinteriors.com</li>
        <li><svg viewBox="0 0 16 16"><path d="M8 1a7 7 0 1 0 0 14A7 7 0 0 0 8 1zm0 2a5 5 0 1 1 0 10A5 5 0 0 1 8 3zm-1 2v3l3 2 1-1-2-1.5V5z" fill-rule="evenodd"/></svg>www.oakridgeinteriors.com</li>
      </ul>
    </div>
  </section>

</main>
</body>
</html>
```